Popup Nightclub Grand Opening Flyer

We need to design a flyer for the grand opening of an upscale, exclusive nightclub called "Lantern". The design needs to be chic and exclusive. The background should be black and the text should primarily be white. We like minimalist designs.

Here is the text for the flyer
-
Velvetroll Atlanta Presents

Lantern (LOGO)

A Popup Nightclub Experience
For one night Only

Friday, October 18, 2013
Party begins at 9PM

INVITE ONLY

See invitation for location details
(Velvetroll Atlanta logo)

-
Examples we like

http://cdn4-x.pressfolio-example.com/sites/default/files/styles/image_content_width/hash/3b/fd/2468013579_4421_flyer.jpg?itok=K9rtQw2z

http://files.hubspace-example.net/files/8Hqq-Tr72WWE3kaRbTmcxP5QZK2F396J8nbRw4CKMHfdX2Y7qSEF-MqjxDoNrLY3QCyQJD7npjGaRq3k-Mhx6hqf3MDSWf8r3/2zenSaturdays.jpg

http://morvex-example.com/wp-content/uploads/siteskin/widgetkit/gallery/2zen/2zen-gen_qstay4-01.jpg

Hi All, one thing that we are seeing that we don't like is on over emphasis on the phrase "a popup nightclub experience" please don't make this the largest thing on the flyer

Target Market(s)

Target market is 25-35 year olds who are affluent (rich) and like luxury brands

Requirements
Must have
• Dark Background
Nice to have
• Velvetroll Logo on the bottom
Modern text that isn't curvy
Should not have
• Curved text

```html
<!DOCTYPE html>
<html lang="en">
<head>
<meta charset="utf-8">
<title>Lantern — A Popup Nightclub Experience</title>
<link rel="stylesheet" href="https://fonts.googleapis.com/css2?family=Jost:wght@300;400;500;600&display=swap">
<style>
  :root {
    --bg: #000000;
    --ice: #e4f0ff;
    --ice-soft: #cfdff2;
    --glow: rgba(150, 200, 255, 0.75);
    --rule: #bfc3c8;
    --rule-dark: #5a5d61;
    --ornament-light: rgba(190, 190, 195, 0.32);
    --ornament-dark: rgba(90, 90, 95, 0.12);
  }
  * { margin: 0; padding: 0; box-sizing: border-box; }
  html, body {
    width: 1200px;
    height: 1080px;
    overflow: hidden;
    background: var(--bg);
  }
  .flyer {
    position: relative;
    width: 1200px;
    height: 1080px;
    background: var(--bg);
    font-family: "Jost", "Futura", sans-serif;
    color: var(--ice);
    text-transform: uppercase;
  }
  .line {
    position: absolute;
    left: 0;
    width: 100%;
    text-align: center;
    white-space: nowrap;
    text-shadow: 0 0 8px var(--glow), 0 0 18px rgba(120, 180, 255, 0.45);
  }
  .ornament {
    position: absolute;
    background: radial-gradient(ellipse at center, var(--ornament-light) 0%, var(--ornament-dark) 55%, rgba(0,0,0,0) 75%);
  }
  .ornament--crest { left: 294px; top: 108px; width: 618px; height: 312px; }
  .ornament--base  { left: 108px; top: 684px; width: 984px; height: 192px; }

  .presenter {
    top: 56px;
    font-size: 27px;
    font-weight: 500;
    letter-spacing: 3px;
  }
  .brand-mark {
    position: absolute;
    left: 528px;
    top: 150px;
    width: 144px;
    height: 144px;
    border-radius: 50%;
    background: var(--ice-soft);
  }
  .brand-name {
    position: absolute;
    left: 0;
    width: 100%;
    top: 340px;
    text-align: center;
    font-size: 64px;
    line-height: 64px;
    font-weight: 300;
    letter-spacing: 12px;
    color: var(--ice-soft);
  }
  .rule-pair {
    position: absolute;
    left: 42px;
    width: 1126px;
    height: 8px;
    border-top: 3px solid var(--rule);
    border-bottom: 2px solid var(--rule-dark);
  }
  .rule-pair--upper { top: 461px; }
  .rule-pair--lower { top: 647px; }

  .headline {
    font-size: 37px;
    line-height: 54px;
    font-weight: 600;
    letter-spacing: 2.5px;
  }
  .headline--first  { top: 509px; }
  .headline--second { top: 563px; }
  .headline-underline {
    position: absolute;
    left: 330px;
    width: 518px;
    top: 624px;
    height: 3px;
    background: var(--ice);
    box-shadow: 0 0 8px var(--glow);
  }
  .event-date {
    top: 655px;
    font-size: 39px;
    line-height: 40px;
    font-weight: 300;
    letter-spacing: 1.5px;
  }
  .event-time {
    top: 697px;
    font-size: 38px;
    line-height: 40px;
    font-weight: 500;
    letter-spacing: 4px;
  }
  .access {
    position: absolute;
    left: 330px;
    width: 520px;
    top: 776px;
    display: flex;
    align-items: center;
    gap: 10px;
  }
  .access-rule {
    flex: 1;
    height: 3px;
    background: var(--ice);
    box-shadow: 0 0 8px var(--glow);
  }
  .access-label {
    font-size: 37px;
    line-height: 44px;
    font-weight: 600;
    letter-spacing: 1px;
    text-shadow: 0 0 8px var(--glow), 0 0 18px rgba(120, 180, 255, 0.45);
  }
  .location-note {
    top: 874px;
    font-size: 22px;
    line-height: 28px;
    font-weight: 500;
    letter-spacing: 2.5px;
  }
  .host-sign {
    position: absolute;
    left: 0;
    width: 100%;
    top: 956px;
    display: flex;
    justify-content: center;
    align-items: center;
    gap: 18px;
  }
  .host-dot {
    width: 40px;
    height: 40px;
    border-radius: 50%;
    background: #ffffff;
  }
  .host-name {
    font-size: 36px;
    line-height: 44px;
    font-weight: 400;
    letter-spacing: 2px;
    color: #ffffff;
  }
</style>
</head>
<body>
  <main class="flyer">
    <div class="ornament ornament--crest" role="img" aria-label="Silver filigree scrollwork crest behind the club name"></div>
    <div class="ornament ornament--base" role="img" aria-label="Silver filigree scrollwork flourish behind the event details"></div>

    <p class="line presenter">Velvetroll Atlanta Presents</p>

    <div class="brand-mark"></div>
    <h1 class="brand-name">Lantern</h1>

    <div class="rule-pair rule-pair--upper"></div>

    <h2 class="line headline headline--first">A Popup Nightclub Experience</h2>
    <h2 class="line headline headline--second">For One Night Only</h2>
    <div class="headline-underline"></div>

    <div class="rule-pair rule-pair--lower"></div>

    <p class="line event-date">Friday, October 18, 2013</p>
    <p class="line event-time">Party Begins at 9PM</p>

    <div class="access">
      <span class="access-rule"></span>
      <span class="access-label">Invite Only</span>
      <span class="access-rule"></span>
    </div>

    <p class="line location-note">See Invitation for Location Details</p>

    <footer class="host-sign">
      <span class="host-dot"></span>
      <span class="host-name">Velvetroll Atlanta</span>
    </footer>
  </main>
</body>
</html>
```